BuildLinkHub.com Full Stationery Design

Business Card will have all info on it. Letterhead will not have name, title or mobile number. Keep general feeling very clean, using colors from the logo as accents.
Name:Dale Marchetti
Title:President
Phone: 1-800-555-0142
Cell: 306-555-0187
email: dale@buildlinkhub.example
website: www.buildlinkhub.example
Address:
PO Box 947
Larkfield, MB
S0J2T0

Target Market(s)

Construction Business owners

Industry/Entity Type

Business

Contact Information for Business Card

Name:Dale Marchetti
Title:President
Phone: 1-800-555-0142
Cell: 306-555-0187
Address:
PO Box 947
Larkfield, MB
S0J2T0

Font styles to use
Sans Serif

Requirements
Must have
• Clean look
Should not have
• Images or cartoon type characters or tools

```html
<!DOCTYPE html>
<html lang="en">
<head>
<meta charset="utf-8">
<title>BuildLinkHub.com Letterhead</title>
<link href="https://fonts.googleapis.com/css2?family=Roboto+Condensed:wght@400;700&display=swap" rel="stylesheet">
<style>
  :root {
    --backdrop: #efd6d1;
    --paper: #ffffff;
    --accent-orange: #e8461e;
    --accent-slate: #5f6f7e;
    --text-grey: #4a4f55;
  }
  * { margin: 0; padding: 0; box-sizing: border-box; }
  html, body {
    width: 1200px;
    height: 784px;
    overflow: hidden;
    background: var(--backdrop);
    font-family: "Roboto Condensed", Arial, sans-serif;
  }
  .letterhead {
    position: absolute;
    left: 338px;
    top: 22px;
    width: 523px;
    height: 740px;
    background: var(--paper);
    box-shadow: 0 6px 18px rgba(120, 70, 60, 0.18);
    overflow: hidden;
  }
  .edge-marker {
    position: absolute;
    top: 22px;
    display: flex;
    gap: 2px;
  }
  .edge-marker span { display: block; width: 12px; height: 3px; }
  .edge-marker .slate { background: var(--accent-slate); }
  .edge-marker .orange { background: var(--accent-orange); }
  .edge-marker--left { left: 0; }
  .edge-marker--right { right: 0; }

  .brand {
    position: absolute;
    top: 58px;
    right: 46px;
    display: flex;
    align-items: center;
    gap: 7px;
  }
  .brand-square {
    width: 14px;
    height: 14px;
    background: var(--accent-orange);
  }
  .brand-name {
    font-size: 17px;
    font-weight: 700;
    color: var(--accent-slate);
    letter-spacing: 0.2px;
  }

  .contact-footer {
    position: absolute;
    left: 190px;
    width: 290px;
    bottom: 44px;
  }
  .contact-rule {
    height: 12px;
    margin-bottom: 8px;
  }
  .contact-rule svg { display: block; }
  .contact-columns {
    display: flex;
    justify-content: space-between;
    font-size: 10.5px;
    font-weight: 400;
    line-height: 1.55;
    color: var(--text-grey);
  }
  .contact-columns .col-right { text-align: right; }

  .bottom-band {
    position: absolute;
    left: 0;
    bottom: 0;
    width: 100%;
    height: 3px;
    display: flex;
  }
  .bottom-band .orange { width: 72%; background: var(--accent-orange); }
  .bottom-band .slate { flex: 1; background: var(--accent-slate); }
</style>
</head>
<body>
  <main class="letterhead">
    <div class="edge-marker edge-marker--left"><span class="slate"></span><span class="orange"></span></div>
    <div class="edge-marker edge-marker--right"><span class="slate"></span><span class="orange"></span></div>

    <header class="brand">
      <span class="brand-square"></span>
      <span class="brand-name">BuildLinkHub.com</span>
    </header>

    <footer class="contact-footer">
      <div class="contact-rule">
        <svg width="290" height="12" viewBox="0 0 290 12" aria-hidden="true">
          <line x1="0" y1="6" x2="108" y2="6" stroke="var(--accent-slate)" stroke-width="1"/>
          <line x1="182" y1="6" x2="290" y2="6" stroke="var(--accent-slate)" stroke-width="1"/>
          <circle cx="118" cy="6" r="5" fill="var(--accent-orange)"/>
          <circle cx="136" cy="6" r="5" fill="var(--accent-orange)"/>
          <circle cx="154" cy="6" r="5" fill="var(--accent-orange)"/>
          <circle cx="172" cy="6" r="5" fill="var(--accent-orange)"/>
        </svg>
      </div>
      <div class="contact-columns">
        <div class="col-left">
          <p>PO Box 947, Larkfield, MB, S0J2T0</p>
          <p>dale@buildlinkhub.example</p>
        </div>
        <div class="col-right">
          <p>1-800-555-0142</p>
          <p>www.buildlinkhub.example</p>
        </div>
      </div>
    </footer>

    <div class="bottom-band"><span class="orange"></span><span class="slate"></span></div>
  </main>
</body>
</html>
```